Ridgeline Journeys business card

please see website
www.ridgelinejourneys.comau

info needed on card
Curtis Halvey
Ph
email
Adventure Riding GPS trails

please use my logo and colours off my site

Curtis Halvey
curtis@ridgelinejourneys.com

```html
<!DOCTYPE html>
<html lang="en">
<head>
<meta charset="utf-8">
<title>Ridgeline Journeys – Business Card</title>
<link href="https://fonts.googleapis.com/css2?family=Arimo:wght@400;700&display=swap" rel="stylesheet">
<style>
  :root {
    --ink: #050505;
    --paper: #ffffff;
    --brand-yellow: #ffd400;
    --brand-yellow-deep: #f2b800;
    --text-light: #f2f2f2;
    --text-grey: #6f6f6f;
    --text-dark: #1b1b1b;
    --stage: #2a2a2a;
  }
  * { box-sizing: border-box; margin: 0; padding: 0; }
  html, body {
    width: 1200px; height: 750px; overflow: hidden;
    background: var(--stage);
    font-family: "Arimo", Arial, sans-serif;
  }
  .sheet {
    width: 1200px; height: 750px;
    display: flex; align-items: center; justify-content: center; gap: 40px;
  }
  .card {
    position: relative;
    width: 540px; height: 309px;
    background: var(--ink);
    overflow: hidden;
    box-shadow: 0 10px 30px rgba(0,0,0,.5);
  }

  /* Back side */
  .card--back {
    display: flex; flex-direction: column; align-items: center; justify-content: center;
    background: radial-gradient(ellipse at 60% 40%, #1a1a1a 0%, var(--ink) 70%);
  }
  .brand {
    display: flex; align-items: center; gap: 12px;
  }
  .brand__dot {
    width: 30px; height: 30px; border-radius: 50%;
    background: var(--brand-yellow);
  }
  .brand__name {
    font-weight: 700; font-size: 26px; letter-spacing: .5px;
  }
  .card--back .brand__name { color: var(--paper); }
  .tagline {
    margin-top: 16px;
    font-size: 14px; letter-spacing: .4px;
  }
  .card--back .tagline { color: var(--text-light); }

  /* Front side */
  .front__shape { position: absolute; inset: 0; }
  .holder {
    position: absolute; left: 36px; top: 70px;
    color: var(--brand-yellow);
    font-weight: 700; font-size: 21px;
  }
  .contact {
    position: absolute; left: 36px; bottom: 36px;
    list-style: none;
    color: var(--text-light); font-size: 13px;
  }
  .contact li { display: flex; align-items: center; gap: 8px; margin-top: 5px; }
  .contact svg { width: 14px; height: 14px; flex: none; }
  .front__brand {
    position: absolute; left: 318px; top: 112px; width: 200px;
  }
  .front__brand .brand { gap: 9px; }
  .front__brand .brand__dot { width: 22px; height: 22px; }
  .front__brand .brand__name { color: var(--text-dark); font-size: 19px; line-height: 1.05; }
  .front__brand .tagline { margin-top: 8px; color: var(--text-grey); font-size: 12px; }
</style>
</head>
<body>
<main class="sheet">

  <section class="card card--back" aria-label="Card back">
    <div class="brand">
      <span class="brand__dot"></span>
      <span class="brand__name">Ridgeline Journeys</span>
    </div>
    <p class="tagline">Adventure Riding GPS trails</p>
  </section>

  <section class="card card--front" aria-label="Card front">
    <svg class="front__shape" viewBox="0 0 540 309" preserveAspectRatio="none" aria-hidden="true">
      <defs>
        <linearGradient id="yellowBand" x1="0" y1="0" x2="0" y2="1">
          <stop offset="0" stop-color="var(--brand-yellow)"/>
          <stop offset="1" stop-color="var(--brand-yellow-deep)"/>
        </linearGradient>
      </defs>
      <path d="M248 0 Q262 235 462 309 L540 309 L540 0 Z" fill="url(#yellowBand)"/>
      <path d="M258 0 Q276 225 486 309 L540 309 L540 0 Z" fill="var(--paper)"/>
    </svg>

    <h1 class="holder">Curtis Halvey</h1>

    <ul class="contact">
      <li>
        <svg viewBox="0 0 16 16" aria-hidden="true"><path fill="var(--brand-yellow)" d="M3.5 1.5l2.5 0 1 3-1.6 1.2a8 8 0 0 0 4.9 4.9L11.5 9l3 1v2.5c0 1-1 2-2 2A11 11 0 0 1 1.5 3.5c0-1 1-2 2-2z"/></svg>
        555 0192 4470
      </li>
      <li>
        <svg viewBox="0 0 16 16" aria-hidden="true"><rect x="1" y="3" width="14" height="10" rx="1" fill="var(--brand-yellow)"/><path d="M1.5 3.5L8 9l6.5-5.5" stroke="var(--ink)" stroke-width="1.3" fill="none"/></svg>
        curtis@ridgelinejourneys.com
      </li>
      <li>
        <svg viewBox="0 0 16 16" aria-hidden="true"><circle cx="8" cy="8" r="7" fill="var(--brand-yellow)"/><path d="M1 8h14M8 1c-3 3-3 11 0 14M8 1c3 3 3 11 0 14" stroke="var(--ink)" stroke-width="1.1" fill="none"/></svg>
        www.ridgelinejourneys.com.au
      </li>
    </ul>

    <div class="front__brand">
      <div class="brand">
        <span class="brand__dot"></span>
        <span class="brand__name">Ridgeline Journeys</span>
      </div>
      <p class="tagline">Adventure Riding GPS trails</p>
    </div>
  </section>

</main>
</body>
</html>
```